Ferncliff Capital - Website Design

We need a website design for a new commercial real estate company called Ferncliff Capital. We're effectively commercial mortgage brokers connecting real estate investors to lenders. We need a website that is simple (not busy), elegant, professional, and user-friendly. A lot of the users will be in their 50's and less tech savvy, so a stream-lined design is best. The website will serve as a portal for lenders to review new financing opportunities, as well as for real estate investors to review terms from lenders.
Updates
Just uploaded our logo.
Target Market(s)
Commercial real estate investors and lenders
Industry/Entity Type
Real Estate
Number of Pages Required
1 page
Colors
Designer to choose colors to be used in the design.
Look and feel

```html
<!DOCTYPE html>
<html lang="en">
<head>
<meta charset="utf-8">
<title>Ferncliff Capital</title>
<link href="https://fonts.googleapis.com/css2?family=Montserrat:wght@400;500;600;700;800&family=Open+Sans:wght@400;600&display=swap" rel="stylesheet">
<style>
:root{
  --blue:#1a8cf0;
  --blue-deep:#0d4fa8;
  --blue-mid:#1372c9;
  --ink:#222831;
  --text:#555b63;
  --light:#f1f1f1;
  --footer:#161a21;
  --white:#ffffff;
}
*{box-sizing:border-box;margin:0;padding:0}
html,body{width:1200px;height:3267px;overflow:hidden}
body{font-family:"Open Sans",Arial,sans-serif;color:var(--text);background:var(--white);position:relative}
h1,h2,h3,h4,.brand,.nav a{font-family:"Montserrat",Arial,sans-serif}
section,header,footer{position:relative;width:1200px}

/* top bar */
.topbar{height:24px;font-size:10px;color:#666;border-bottom:1px solid #eee;position:relative}
.topbar span{position:absolute;top:5px;white-space:nowrap}
.topbar .search{position:absolute;right:161px;top:0;width:30px;height:24px;background:var(--blue)}
.topbar .search svg{position:absolute;left:9px;top:6px}

/* header */
.site-header{height:84px}
.brand{position:absolute;left:161px;top:28px;font-size:22px;font-weight:500;color:var(--ink);white-space:nowrap}
.brand b{color:var(--blue);font-weight:700}
.nav{position:absolute;right:161px;top:35px;display:flex;gap:30px}
.nav a{font-size:12px;font-weight:500;color:#444;text-decoration:none;text-transform:uppercase;padding-bottom:14px}
.nav a.active{border-bottom:2px solid var(--blue);color:var(--ink)}

/* hero */
.hero{height:449px;overflow:hidden}
.hero-photo{position:absolute;inset:0;background:linear-gradient(90deg,#c9d3de 0%,#e7ecf1 40%,#f4f6f8 65%,#dfe6ee 100%)}
.hero h1{position:absolute;left:592px;top:168px;font-size:29px;line-height:35px;font-weight:800;color:var(--blue);width:470px}
.hero p{position:absolute;left:592px;top:240px;font-size:15px;line-height:28px;color:#222;width:430px}
.hero .arrow{position:absolute;top:372px;width:40px;height:40px;border:2px solid var(--blue);border-radius:50%;background:rgba(255,255,255,.6)}
.hero .arrow svg{position:absolute;left:11px;top:11px}

/* services */
.services{height:451px;color:var(--white);overflow:hidden}
.services-photo{position:absolute;inset:0;background:radial-gradient(circle at 15% 20%,#3f8ee6 0%,#1a5fc4 35%,#0c3f95 100%)}
.section-title{position:absolute;left:0;width:1200px;text-align:center;font-size:28px;font-weight:700}
.services .section-title{top:48px;color:var(--white)}
.service{position:absolute;top:140px;width:280px;text-align:center}
.service svg{display:block;margin:0 auto}
.service h3{font-size:18px;font-weight:700;margin-top:22px}
.service p{font-size:11px;line-height:22px;margin:12px auto 0;width:235px;color:#e4eeff}
.btn-sm{display:inline-block;margin-top:12px;background:var(--blue);color:var(--white);font-size:11px;padding:6px 14px;border-radius:14px}

/* projects */
.projects{height:749px}
.projects .section-title{top:40px;color:var(--blue)}
.tile{position:absolute;color:var(--white);text-align:center;display:flex;flex-direction:column;justify-content:center;align-items:center}
.tile h4{font-size:20px;line-height:26px;font-weight:700;text-shadow:0 1px 3px rgba(0,0,0,.4)}
.tile .date{font-size:13px;margin-top:8px}
.t1{background:linear-gradient(160deg,#2d3c55,#6a5d4a 70%,#3a3530)}
.t2{background:linear-gradient(170deg,#9aa3ad,#4c5a66 55%,#2b3a32)}
.t3{background:linear-gradient(150deg,#8fb0d8,#2a4f82 60%,#1b2b44)}
.t4{background:linear-gradient(160deg,#c9c4bb,#7c7368 60%,#3b3632)}
.t5{background:linear-gradient(160deg,#b8b2a8,#5f5a55 60%,#2e2b29)}

/* newsletter */
.newsletter{height:159px;background:var(--light)}
.newsletter h3{position:absolute;font-size:19px;font-weight:500;color:var(--ink);white-space:nowrap}
.newsletter .input{position:absolute;left:257px;top:77px;width:290px;height:36px;background:var(--white);border-radius:18px;font-size:11px;color:#999;padding:11px 18px}
.newsletter .subscribe{position:absolute;left:545px;top:77px;width:160px;height:38px;background:var(--blue);border-radius:19px;color:var(--white);font-family:"Montserrat",sans-serif;font-weight:700;font-size:17px;text-align:center;line-height:38px}
.social{position:absolute;left:732px;top:84px;display:flex;gap:6px}
.social i{display:block;width:22px;height:22px;background:#4a6fa5}

/* testimonials */
.testimonials{height:477px;color:var(--white);overflow:hidden}
.testimonials-bg{position:absolute;inset:0;background:linear-gradient(135deg,#0f78cf,#2a9be6 50%,#0c6bc0)}
.testimonials .section-title{top:50px}
.quote{position:absolute;top:146px;width:210px;text-align:center}
.avatar{width:92px;height:92px;border-radius:50%;margin:0 auto;background:linear-gradient(#d9c7b5,#8c6f59);border:3px solid rgba(255,255,255,.8)}
.quote p{font-size:11px;line-height:21px;margin-top:24px;color:#e8f3ff}
.quote h4{font-size:13px;font-weight:700;margin-top:16px}
.dots{position:absolute;top:417px;left:560px;display:flex;gap:14px}
.dots i{width:5px;height:5px;border-radius:50%;background:var(--white)}

/* certifications */
.certs{height:172px}
.certs .section-title{top:38px;color:var(--ink)}
.badge{position:absolute;top:98px;height:40px;background:#9a9a9a}

/* contact */
.contact{height:384px}
.contact-side{position:absolute;left:0;top:0;width:601px;height:384px;background:#f3f3f3}
.contact h2{position:absolute;left:161px;top:42px;font-size:28px;font-weight:700;color:var(--ink)}
.field{position:absolute;left:161px;width:314px;background:var(--white);border:1px solid #eee}
.send{position:absolute;left:161px;top:310px;width:89px;height:28px;border-radius:14px;background:var(--blue);color:var(--white);font-size:11px;font-weight:700;text-align:center;line-height:28px;font-family:"Montserrat",sans-serif}
.map{position:absolute;left:601px;top:0;width:599px;height:384px;background:linear-gradient(135deg,#e7e8ea,#dcdee1)}

/* footer */
.site-footer{height:318px;background:var(--footer);color:#c9ccd1}
.site-footer .brand{top:38px;color:var(--white)}
.fnav{position:absolute;right:161px;top:44px;display:flex;gap:34px;font-size:12px;color:var(--white)}
.fdiv{position:absolute;left:161px;right:161px;top:84px;height:1px;background:#2b313a}
.fcol{position:absolute;top:108px;font-size:11px;line-height:22px}
.fcol h4{color:var(--white);font-size:13px;font-weight:700;margin-bottom:10px}
.fcol ul{list-style:none}
.fcol li::before{content:"›";color:var(--blue);margin-right:12px}
.crow{display:flex;gap:12px;align-items:flex-start;margin-bottom:10px}
.crow svg{flex:none;margin-top:4px}
.copy{position:absolute;left:0;width:1200px;top:278px;text-align:center;font-size:10.5px;color:#cfd2d6}
</style>
</head>
<body>

<div class="topbar">
  <span style="left:161px">✆ 24/7 Support At any time &nbsp;&nbsp;&nbsp; ✆ Call Us +1 800 555 0142</span>
  <span style="left:815px">⌖ 123 Lorem Ipsum Dolor Amit, NZ</span>
  <div class="search"><svg width="12" height="12" viewBox="0 0 12 12"><circle cx="5" cy="5" r="3.5" fill="none" stroke="#fff" stroke-width="1.6"/><line x1="7.6" y1="7.6" x2="11" y2="11" stroke="#fff" stroke-width="1.6"/></svg></div>
</div>

<header class="site-header">
  <div class="brand">Ferncliff <b>Capital</b></div>
  <nav class="nav"><a class="active">Home</a><a>About Us</a><a>Services</a><a>Contact</a></nav>
</header>

<section class="hero">
  <div class="hero-photo" role="img" aria-label="Business team of three reviewing documents in a bright glass office"></div>
  <h1>WE ARE A NEW COMMERCIAL REAL ESTATE COMPANY.</h1>
  <p>We're effectively commercial mortgage brokers connecting real estate investors to lenders.</p>
  <div class="arrow" style="left:940px"><svg width="14" height="14" viewBox="0 0 14 14"><path d="M9 3L5 7l4 4z" fill="#1a8cf0"/></svg></div>
  <div class="arrow" style="left:993px"><svg width="14" height="14" viewBox="0 0 14 14"><path d="M5 3l4 4-4 4z" fill="#1a8cf0"/></svg></div>
</section>

<section class="services">
  <div class="services-photo" role="img" aria-label="Hands holding wooden blocks shaped like a house labelled mortgage on a blue bokeh background"></div>
  <h2 class="section-title">OUR SERVICES</h2>
  <div class="service" style="left:160px">
    <svg width="40" height="46" viewBox="0 0 40 46"><rect x="8" y="2" width="24" height="42" fill="none" stroke="#fff" stroke-width="3"/><g fill="#fff"><rect x="13" y="8" width="4" height="4"/><rect x="23" y="8" width="4" height="4"/><rect x="13" y="17" width="4" height="4"/><rect x="23" y="17" width="4" height="4"/><rect x="13" y="26" width="4" height="4"/><rect x="23" y="26" width="4" height="4"/><rect x="17" y="35" width="6" height="9"/></g></svg>
    <h3>Commercial</h3>
    <p>Sed ut perspiciatis unde omnis iste natus error sit voluptatem accusantium doloremque laudantium, totam rem aperiam, eaque ipsa quae ab illo inventore...</p>
    <span class="btn-sm">Read More</span>
  </div>
  <div class="service" style="left:459px">
    <svg width="56" height="46" viewBox="0 0 56 46"><g fill="#fff"><circle cx="28" cy="12" r="8"/><circle cx="12" cy="16" r="6"/><circle cx="44" cy="16" r="6"/><path d="M14 44c0-10 6-18 14-18s14 8 14 18z"/><path d="M0 42c0-8 5-14 12-14 2 0 4 .5 5 1.5C13 33 11 38 11 42z"/><path d="M56 42c0-8-5-14-12-14-2 0-4 .5-5 1.5 4 3.5 6 8.5 6 12.5z"/></g></svg>
    <h3>Financial Investors</h3>
    <p>Sed ut perspiciatis unde omnis iste natus error sit voluptatem accusantium doloremque laudantium, totam rem aperiam, eaque ipsa quae ab illo inventore...</p>
    <span class="btn-sm">Read More</span>
  </div>
  <div class="service" style="left:757px">
    <svg width="50" height="46" viewBox="0 0 50 46"><path d="M4 4v38h44" fill="none" stroke="#fff" stroke-width="3"/><path d="M8 40V26l10-12 10 10 16-18v34z" fill="#fff"/></svg>
    <h3>Projects</h3>
    <p>Sed ut perspiciatis unde omnis iste natus error sit voluptatem accusantium doloremque laudantium, totam rem aperiam, eaque ipsa quae ab illo inventore...</p>
    <span class="btn-sm">Read More</span>
  </div>
</section>

<section class="projects">
  <h2 class="section-title">PROJECTS</h2>
  <div class="tile t1" style="left:161px;top:90px;width:499px;height:337px" role="img" aria-label="Modern glass apartment building at dusk">
    <h4>DUIS AUTE IRURE DOLOR IN</h4><span class="date">◷ AUGUST 6, 2017</span></div>
  <div class="tile t2" style="left:671px;top:90px;width:368px;height:337px" role="img" aria-label="Glass office towers above trees">
    <h4>EXCEPTEUR SINT OCCAECAT</h4><span class="date">◷ AUGUST 6, 2017</span></div>
  <div class="tile t3" style="left:161px;top:438px;width:285px;height:266px" role="img" aria-label="Skyscraper seen from below against a blue sky">
    <h4>DUIS AUTE IRURE<br>DOLOR IN</h4><span class="date">◷ AUGUST 6, 2017</span></div>
  <div class="tile t4" style="left:457px;top:438px;width:286px;height:266px" role="img" aria-label="Engineers reviewing plans at a construction site">
    <h4>DUIS AUTE IRURE<br>DOLOR IN</h4><span class="date">◷ AUGUST 6, 2017</span></div>
  <div class="tile t5" style="left:754px;top:438px;width:285px;height:266px" role="img" aria-label="Business people talking in an office">
    <h4>DUIS AUTE IRURE<br>DOLOR IN</h4><span class="date">◷ AUGUST 6, 2017</span></div>
</section>

<section class="newsletter">
  <h3 style="left:266px;top:40px">Newsletter Subscribe</h3>
  <div class="input">Enter Email Id</div>
  <div class="subscribe">Subscribe</div>
  <h3 style="left:730px;top:42px">Stay Connected</h3>
  <div class="social" aria-label="Social links"><i></i><i></i><i></i><i></i><i></i><i></i></div>
</section>

<section class="testimonials">
  <div class="testimonials-bg" role="img" aria-label="Blue low-poly geometric background"></div>
  <h2 class="section-title">CLIENTS TESTIMONIALS</h2>
  <div class="quote" style="left:239px"><div class="avatar" role="img" aria-label="Client portrait"></div>
    <p>Sed ut perspiciatis unde omnis iste natus error sit voluptatem accusantium do loremque laudantium, totam rem aperiam, eaque.</p><h4>-Marcus Lane</h4></div>
  <div class="quote" style="left:496px"><div class="avatar" role="img" aria-label="Client portrait"></div>
    <p>Sed ut perspiciatis unde omnis iste natus error sit voluptatem accusantium do loremque laudantium, totam rem aperiam, eaque.</p><h4>- Elena Ruiz</h4></div>
  <div class="quote" style="left:751px"><div class="avatar" role="img" aria-label="Client portrait"></div>
    <p>Sed ut perspiciatis unde omnis iste natus error sit voluptatem accusantium do loremque laudantium, totam rem aperiam, eaque.</p><h4>- Tomas Reid</h4></div>
  <div class="dots"><i></i><i></i><i></i><i></i></div>
</section>

<section class="certs">
  <h2 class="section-title">CERTIFICATIONS</h2>
  <div class="badge" style="left:224px;width:46px"></div>
  <div class="badge" style="left:310px;width:210px;height:14px;top:111px"></div>
  <div class="badge" style="left:557px;width:42px;border-radius:50%"></div>
  <div class="badge" style="left:644px;width:166px;height:18px;top:109px"></div>
  <div class="badge" style="left:850px;width:124px;height:32px;top:102px"></div>
</section>

<section class="contact">
  <div class="contact-side"></div>
  <h2>SEND US A MESSAGE</h2>
  <div class="field" style="top:105px;height:34px"></div>
  <div class="field" style="top:151px;height:34px"></div>
  <div class="field" style="top:195px;height:88px"></div>
  <div class="send">SEND</div>
  <div class="map" role="img" aria-label="Street map of the office location"></div>
</section>

<footer class="site-footer">
  <div class="brand">Ferncliff <b>Capital</b></div>
  <div class="fnav"><span>Home</span><span>About Us</span><span>Services</span><span>Contact Us</span></div>
  <div class="fdiv"></div>
  <div class="fcol" style="left:161px;width:290px">
    <h4>ABOUT</h4>
    <p>Sed ut perspiciatis unde omnis iste natus error sit voluptatem accusantium doloremque laudantium, totam rem aperiam, eaque ipsa quae ab illo inventore veritatis et quasi architecto beatae.</p>
  </div>
  <div class="fcol" style="left:575px">
    <h4>SERVICES</h4>
    <ul><li>Construction</li><li>Projects</li><li>Commercial</li><li>Financial Support</li></ul>
  </div>
  <div class="fcol" style="left:882px;width:170px">
    <h4>CONTACT US</h4>
    <div class="crow"><svg width="12" height="16" viewBox="0 0 12 16"><path d="M6 0a6 6 0 016 6c0 4-6 10-6 10S0 10 0 6a6 6 0 016-6z" fill="#1a8cf0"/><circle cx="6" cy="6" r="2" fill="#161a21"/></svg><span>Main Store 418 Harlow Ave<br>Westbridge</span></div>
    <div class="crow"><svg width="12" height="12" viewBox="0 0 12 12"><path d="M2 0l3 3-1.5 2c1 2 2 3 3.5 3.5L9 7l3 3-2 2C5 12 0 7 0 2z" fill="#1a8cf0"/></svg><span>(346) 555-0187</span></div>
    <div class="crow"><svg width="13" height="10" viewBox="0 0 13 10"><rect width="13" height="10" fill="#1a8cf0"/><path d="M0 0l6.5 5L13 0" fill="none" stroke="#161a21"/></svg><span>info@ferncliffcap.com</span></div>
  </div>
  <div class="copy">Copyrights © 2017, www.ferncliffcap.com &nbsp;|&nbsp; Privacy Policy &nbsp;|&nbsp; Terms Of Use</div>
</footer>

</body>
</html>
```